Belvascotravel.com web design project + logo design

Hi,

We are a Russian online tour operator - sunkettle.com

We are looking to tranmsfer our domain to belvascotravel.com. The website and logo need to be belvascoesque - we are not looking to change our functionality, but we need to make the website much more attracitve to clients, much more wild looking but at the same time remaining a professional travel company.

The main concept of the website should be innovative travel (as belvasco was an innovator). Alternatively, you could go down the artist route and go down the draw / design your own tour road.

On our website the customer is able to combine travel services (hotels, flights, Visa services, and soon chauffeur, car rental etc...) put it into their basket (the basket definitely has to look better than it is at the moment) and pay for it in one go by card.

We are also stressin our customer support with web chat, call centre etc... (call centre number at the top of the page)

We aim to provide an easy user experience, but we need to make it have some more style, so I will be waiting for what you guys can come up with.
Let me know if you have any questions - skype is: mrdolbarin

Industry/Entity Type

It Company

Requirements
Must have
• It is quite a simple task - to take the existing website sunkettle.com and belvascosize it to create belvascotravel.com, the functionality of the website will remain the same and there are not many pages in the website. Homepage, Checkout step1, Checkout step 2 (you can view both of these if you select a service) and the generic pages for T&C''s, Privacy policy etc...

IMPORTANT UPDATE

We are also looking at how the search results will look in the designs, (please do a search on our website for hotel / flight)

```html
<!DOCTYPE html>
<html lang="en">
<head>
<meta charset="utf-8">
<title>Belvasco Travel</title>
<link href="https://fonts.googleapis.com/css2?family=Figtree:wght@400;600;700;800&display=swap" rel="stylesheet">
<style>
:root{
  --teal:#1aa6c6;
  --teal-dark:#1190ad;
  --gray:#616161;
  --gray-dark:#2f2f2f;
  --gray-text:#555;
  --light:#f2f2f2;
  --orange:#e8450f;
  --orange-light:#f2651c;
  --white:#fff;
}
*{box-sizing:border-box;margin:0;padding:0}
html,body{width:1122px;height:1200px;overflow:hidden;background:var(--white);font-family:"Figtree",Arial,sans-serif;color:var(--gray-text)}
.page{position:relative;width:1122px;height:1200px;overflow:hidden}
.abs{position:absolute}

/* header */
.topbar{left:0;top:0;width:1122px;height:48px;background:linear-gradient(#fafafa,#ececec);border-bottom:1px solid #ddd;z-index:3}
.head-item{z-index:5}
.brand{left:187px;top:0;width:138px;height:86px;background:#efefef;box-shadow:0 2px 4px rgba(0,0,0,.18);z-index:6;display:flex;align-items:center;justify-content:center;text-align:center;color:#555;font-weight:700;font-size:17px;line-height:1.15;letter-spacing:1px}
.phone{left:350px;top:15px;color:var(--teal);font-weight:700;font-size:16px;display:flex;align-items:center;gap:4px}
.webchat{left:497px;top:15px;color:var(--teal);font-weight:700;font-size:16px;display:flex;align-items:center;gap:3px}
.lang{left:605px;top:11px;width:109px;height:26px;background:#fff;border:1px solid #ddd;border-radius:2px;display:flex;align-items:center;padding-left:6px;gap:6px;color:var(--teal);font-weight:700;font-size:13.5px}
.flag{width:15px;height:10px;background:#2a4a8f;position:relative;overflow:hidden}
.flag::before{content:"";position:absolute;left:6px;top:0;width:3px;height:10px;background:#d22}
.flag::after{content:"";position:absolute;left:0;top:3.5px;width:15px;height:3px;background:#d22}
.caret{margin-left:auto;padding:0 7px;border-left:1px solid #ccc;font-size:9px;line-height:14px}
.btn-forum{left:726px;top:11px;width:88px;height:26px;background:var(--teal);color:#fff;font-weight:700;font-size:13.5px;display:flex;align-items:center;justify-content:center;gap:8px;border-radius:2px;box-shadow:0 2px 0 var(--teal-dark)}
.btn-tour{left:824px;top:11px;width:111px;height:26px;background:#6a6a6a;color:#fff;font-weight:700;font-size:13.5px;display:flex;align-items:center;padding-left:10px;gap:6px;border-radius:2px;box-shadow:0 2px 0 #444}
.btn-tour .caret{border-left-color:#999;color:#fff}

/* hero */
.hero{left:0;top:48px;width:1122px;height:336px;background:linear-gradient(#bfe3f3,#e6f4fa 60%,#f6fbfd);overflow:hidden}
.skyline{left:190px;top:180px;width:743px;height:156px;background:linear-gradient(90deg,#1aa6c6 0%,#5d6066 28%,#1aa6c6 45%,#6a6c70 62%,#1aa6c6 78%,#35c6e6 100%);opacity:.92;border-radius:40px 40px 0 0}
.hero-text{z-index:2}
.h-flights{left:238px;top:112px;font-size:48px;font-weight:800;color:#5a5a5a;letter-spacing:-1px;line-height:1}
.h-sub1{left:326px;top:156px;font-size:15px;font-weight:700;color:var(--teal)}
.h-hotels{left:326px;top:168px;font-size:48px;font-weight:800;color:#5a5a5a;letter-spacing:-1px;line-height:1}
.h-sub2{left:414px;top:208px;font-size:15px;font-weight:700;color:var(--teal)}

/* tabs */
.tabs{left:450px;top:402px;width:220px;height:24px;display:flex;gap:1px}
.tab{flex:1;display:flex;align-items:center;justify-content:center;font-size:10.5px;text-transform:uppercase;background:#f3f3f3;color:#777;border-bottom:2px solid #ddd}
.tab.active{background:var(--teal);color:#fff;border-bottom-color:var(--teal-dark)}

/* search panel */
.search{left:187px;top:438px;width:748px;height:252px;background:var(--gray-dark)}
.search-form{left:187px;top:438px;width:506px;height:252px;background:var(--gray)}
.lbl{font-size:12px;color:#eee;text-align:right}
.lbl.left{left:0;width:94px}
.lbl.right{left:250px;width:69px}
.field{height:20px;background:#fff;border:1px solid #ddd;box-shadow:inset 0 1px 2px rgba(0,0,0,.1)}
.check{font-size:12px;color:#eee;display:flex;align-items:center;gap:5px}
.check i{display:block;width:9px;height:9px;background:#fff}
.btn-search{left:513px;top:527px;width:156px;height:27px;background:linear-gradient(var(--orange-light),var(--orange));color:#fff;font-weight:700;font-size:14px;display:flex;align-items:center;justify-content:center;box-shadow:0 2px 0 #a52d06}
.calendar{left:210px;top:568px;width:459px;height:109px;background:#fff;box-shadow:0 2px 3px rgba(0,0,0,.3)}
.cal-month{left:11px;top:8px;font-size:11.5px;font-weight:700;color:var(--teal)}
.cal-grid{left:11px;top:24px;width:440px;height:75px;border:1px solid #ccc;border-radius:0 0 3px 3px}
.cal-head{display:flex;height:19px;background:linear-gradient(#757575,#555)}
.cal-head span{flex:1;color:#fff;font-size:9.5px;font-weight:600;display:flex;align-items:center;justify-content:center;border-right:1px solid #888}
.cal-head span:last-child{border-right:0}
.perf{left:690px;top:454px;width:6px;height:220px;background:radial-gradient(circle,#fff 2.6px,transparent 3px) 0 0/6px 19.2px repeat-y}
.basket{left:714px;top:455px;width:202px;height:219px;background:#fff;box-shadow:0 2px 0 #bbb}
.basket-title{left:0;top:10px;width:202px;text-align:center;font-size:21px;font-weight:800;color:var(--teal)}
.basket-icon{left:18px;top:40px;width:167px;height:80px;background:var(--teal);border-radius:2px;box-shadow:0 3px 0 var(--teal-dark);display:flex;align-items:center;justify-content:center}
.badge{left:162px;top:33px;width:38px;height:38px;border-radius:50%;background:#5a5a5a;border:2px solid #ddd;color:#fff;font-weight:700;font-size:19px;display:flex;align-items:center;justify-content:center}
.btn-pay{left:18px;top:152px;width:167px;height:33px;background:linear-gradient(var(--orange-light),var(--orange));color:#fff;font-weight:700;font-size:15px;display:flex;align-items:center;justify-content:center;box-shadow:0 2px 0 #a52d06}
.pricing{left:0;top:197px;width:202px;text-align:center;font-size:11.5px;color:var(--teal)}

/* info section */
.features{left:0;top:712px;width:1122px;height:304px;background:var(--light)}
.card{top:742px;width:231px;height:237px;background:#fff;box-shadow:0 1px 3px rgba(0,0,0,.12)}
.ribbon{left:-4px;top:8px;width:175px;height:32px;color:#fff;font-size:22px;font-weight:800;display:flex;align-items:center;padding-left:16px;clip-path:polygon(0 0,95% 0,100% 50%,95% 100%,0 100%)}
.ribbon.teal{background:var(--teal)}
.ribbon.gray{background:#616161;padding-left:20px}
.card-lead{left:16px;top:54px;font-size:11.5px;font-weight:600;color:#444}
.card-title{left:17px;top:52px;font-size:15px;font-weight:700;color:#555}
.card-body{left:17px;top:76px;width:196px;font-size:9.5px;line-height:12.7px;color:#666}
.visa{top:80px;width:97px;height:40px;background:linear-gradient(#6e6e6e,#555);color:#fff;text-align:center;border-radius:2px;box-shadow:0 2px 0 #3a3a3a;padding-top:4px}
.visa small{display:block;font-size:11.5px;font-weight:600;line-height:12px}
.visa b{display:block;font-size:17px;font-weight:800;line-height:19px}
.more{left:16px;top:208px;font-size:13px;font-weight:800;color:var(--teal)}

/* footer */
.footer{left:0;top:1016px;width:1122px;height:122px;background:linear-gradient(#7a7a7a,#6a6a6a)}
.fcol h4{font-size:13.5px;font-weight:700;color:#fff;margin-bottom:9px}
.fcol p{font-size:10px;color:#f0f0f0;line-height:15.8px}
.email{left:670px;top:1063px;width:169px;height:27px;background:#fff;font-size:11px;color:#aaa;padding:7px 10px}
.subscribe{left:845px;top:1063px;width:85px;height:26px;background:var(--teal);color:#fff;font-weight:700;font-size:13px;display:flex;align-items:center;justify-content:center;box-shadow:0 2px 0 var(--teal-dark)}
.fnote{left:672px;top:1095px;font-size:8.5px;color:#eee}
.bottom{left:0;top:1138px;width:1122px;height:62px;background:#626262}
.foot-brand{left:189px;top:1150px;color:#e8e8e8;font-size:13px;font-weight:700;line-height:1.15;letter-spacing:1px}
.copy{left:508px;top:1165px;font-size:8.5px;color:#eee}
.social-label{left:776px;top:1160px;font-size:13px;font-weight:700;color:#fff}
.dot{top:1154px;width:27px;height:27px;border-radius:50%;background:#fff}
</style>
</head>
<body>
<div class="page">

  <header>
    <div class="abs topbar"></div>
    <div class="abs brand">BELVASCO<br>TRAVEL</div>
    <div class="abs head-item phone">
      <svg width="11" height="13" viewBox="0 0 11 13"><path d="M2 1l2 0 1 3-1.5 1c.6 1.6 1.6 2.8 3 3.5L8 7l3 1.2V10.5C11 11.5 10 12.2 9 12 4.5 11 1 7 .8 2.5 .8 1.5 1.3 1 2 1z" fill="#666"/></svg>
      8-800-555-0147
    </div>
    <div class="abs head-item webchat">
      <svg width="16" height="12" viewBox="0 0 16 12"><ellipse cx="6" cy="5" rx="6" ry="4.2" fill="#666"/><ellipse cx="11" cy="7" rx="5" ry="3.6" fill="#666"/><path d="M3 8l-1 3 3-2z" fill="#666"/></svg>
      Web Chat
    </div>
    <div class="abs head-item lang"><span class="flag"></span>English<span class="caret">▼</span></div>
    <div class="abs head-item btn-forum">
      <svg width="14" height="11" viewBox="0 0 14 11"><ellipse cx="7" cy="4.6" rx="7" ry="4.4" fill="#fff"/><path d="M3 7l-1 4 4-3z" fill="#fff"/></svg>
      Forum
    </div>
    <div class="abs head-item btn-tour">
      <svg width="11" height="12" viewBox="0 0 11 12"><circle cx="5.5" cy="3.2" r="3" fill="#fff"/><path d="M0 12c0-4 2.5-5.5 5.5-5.5S11 8 11 12z" fill="#fff"/></svg>
      My Tour<span class="caret">▼</span>
    </div>
  </header>

  <section class="abs hero">
    <div class="abs skyline" role="img" aria-label="Illustrated skyline of world landmarks in teal and grey"></div>
  </section>
  <div class="abs hero-text h-flights">Flights</div>
  <div class="abs hero-text h-sub1">from Tours designer</div>
  <div class="abs hero-text h-hotels">Hotels</div>
  <div class="abs hero-text h-sub2">by City Builders</div>

  <nav class="abs tabs">
    <div class="tab active">Tickets</div>
    <div class="tab">Info</div>
    <div class="tab">Hotels</div>
  </nav>

  <section class="abs search"></section>
  <section class="abs search-form">
    <div class="abs lbl left" style="top:18px">Whence</div>
    <div class="abs lbl left" style="top:45px">There</div>
    <div class="abs lbl left" style="top:72px">Passengers</div>
    <div class="abs lbl left" style="top:99px">Class</div>
    <div class="abs field" style="left:101px;top:15px;width:156px"></div>
    <div class="abs field" style="left:101px;top:42px;width:156px"></div>
    <div class="abs field" style="left:101px;top:69px;width:156px"></div>
    <div class="abs field" style="left:101px;top:96px;width:156px"></div>
    <div class="abs lbl right" style="top:18px">Where</div>
    <div class="abs lbl right" style="top:45px">Back</div>
    <div class="abs field" style="left:326px;top:15px;width:156px"></div>
    <div class="abs field" style="left:326px;top:42px;width:156px"></div>
    <div class="abs check" style="left:326px;top:68px"><i></i>Back</div>
    <div class="abs check" style="left:380px;top:68px"><i></i>One Way</div>
  </section>
  <div class="abs btn-search">SEARCH</div>
  <div class="abs calendar">
    <div class="abs cal-month">JANUARY</div>
    <div class="abs cal-grid">
      <div class="cal-head"><span>Monday</span><span>Tuesday</span><span>Wednesday</span><span>Thursday</span><span>Friday</span><span>Saturday</span><span>Sunday</span></div>
    </div>
  </div>
  <div class="abs perf"></div>

  <aside class="abs basket">
    <div class="abs basket-title">BASKET</div>
    <div class="abs basket-icon">
      <svg width="92" height="66" viewBox="0 0 92 66">
        <path d="M10 4l16 20M82 4L66 24" stroke="#fff" stroke-width="7" stroke-linecap="round"/>
        <rect x="2" y="26" width="88" height="12" rx="3" fill="#fff"/>
        <path d="M10 40h72l-6 24H16z" fill="#fff"/>
        <rect x="30" y="44" width="6" height="16" fill="#1aa6c6"/>
        <rect x="43" y="44" width="6" height="16" fill="#1aa6c6"/>
        <rect x="56" y="44" width="6" height="16" fill="#1aa6c6"/>
      </svg>
    </div>
    <div class="abs badge">0</div>
    <div class="abs btn-pay">PAYMENT</div>
    <div class="abs pricing">*Pricing</div>
  </aside>

  <section class="abs features"></section>

  <article class="abs card" style="left:187px">
    <div class="abs ribbon teal">INFO</div>
    <div class="abs card-lead">There are two options apply for a visa</div>
    <div class="abs visa" style="left:14px"><small>Visa</small><b>ONLINE</b></div>
    <div class="abs visa" style="left:119px"><small>Visa</small><b>MY SELF</b></div>
    <p class="abs card-body" style="top:137px">Lorem ipsum dolor sit amet, consectetuer adipiscing elit, sed diam nonummy nibh euismod tincidunt ut laoreet dolore magna aliquam erat volutpat. Ut wisi enim ad minim veniam, quis nostrud exerci tation.</p>
    <div class="abs more">›› READ MORE</div>
  </article>

  <article class="abs card" style="left:445px">
    <div class="abs ribbon gray">TICKETS</div>
    <h3 class="abs card-title">Flights from Tours designer</h3>
    <p class="abs card-body">On our site you can consider offers from different airlines and purchase tickets according to your wishes and budget. Plan dates of departures and arrivals c in any country, filling the cells you want, Tour Designer automatically displays your program in the calendar.<br>On Tour Designer You can create any tour, including round-the-world and pay for all the services a single payment.</p>
    <div class="abs more">›› READ MORE</div>
  </article>

  <article class="abs card" style="left:702px">
    <div class="abs ribbon teal">HOTELS</div>
    <h3 class="abs card-title">Hotels by City Builder</h3>
    <p class="abs card-body">Our site offers a wide selection of hotels located in different countries and continents of the world. You can choose and book all kinds of accommodation options, according to your wishes and budget.<br>pursue their dreams!<br>We have created for you the most convenient framework for planning a vacation or business trip.</p>
    <div class="abs more">›› READ MORE</div>
  </article>

  <footer>
    <div class="abs footer"></div>
    <div class="abs fcol" style="left:189px;top:1034px"><h4>View Site</h4><p>Home<br>About Us<br>Forum<br>Contacts</p></div>
    <div class="abs fcol" style="left:286px;top:1034px"><h4>Help</h4><p>Help<br>Terms of use<br>Privacy Policy<br>Cookies</p></div>
    <div class="abs fcol" style="left:374px;top:1034px"><h4>Find us</h4><p>Sun Kettle Limited<br>14 Harrow Lane<br>London, N4 2QT<br>UK</p></div>
    <div class="abs fcol" style="left:526px;top:1034px"><h4>Contact Us</h4><p style="padding-top:3px">+7 (495) 555-01-62<br>info@sunkettle.com</p></div>
    <div class="abs fcol" style="left:670px;top:1034px"><h4>Exclusive Offers</h4></div>
    <div class="abs email">Email Address ...</div>
    <div class="abs subscribe">Subscribe</div>
    <div class="abs fnote">Your data is safe, read our Privacy Policy</div>

    <div class="abs bottom"></div>
    <div class="abs foot-brand">BELVASCO<br>TRAVEL</div>
    <div class="abs copy">2013 © Belvascotravel.com</div>
    <div class="abs social-label">We are in:</div>
    <div class="abs dot" style="left:847px"></div>
    <div class="abs dot" style="left:878px"></div>
    <div class="abs dot" style="left:908px"></div>
  </footer>

</div>
</body>
</html>
```